Yard sign

Looking for a yard sign. <br/>Something simple, name, number. <br/>Large text, readable from 50 feet away. <br/><br/>18 x 24 inches.

Target Market(s)

Potential homeowners thinking about going solar.

Colors

Designer to choose colors to be used in the design.

Requirements
Must have
• "WE'VE GONE SOLAR!"
Nice to have
• We are a solar company, we would like a design that compliments the homeowners decision that they went solar and encourages others to do the same.

```html
<!DOCTYPE html>
<html lang="en">
<head>
<meta charset="utf-8">
<title>We've Gone Solar – Yard Sign</title>
<link rel="stylesheet" href="https://fonts.googleapis.com/css2?family=Jost:wght@500;600;700&display=swap">
<style>
  :root {
    --sun-orange: #F5922A;
    --sign-white: #FFFFFF;
    --page-bg: #FFFFFF;
  }
  html, body {
    margin: 0;
    padding: 0;
    width: 1200px;
    height: 900px;
    overflow: hidden;
    background: var(--page-bg);
  }
  .yard-sign {
    display: block;
    width: 1200px;
    height: 900px;
    font-family: "Jost", "Futura", sans-serif;
  }
  .sign-outline { fill: var(--sign-white); stroke: var(--sun-orange); stroke-width: 6; }
  .sign-footer { fill: var(--sun-orange); }
  .headline { fill: var(--sun-orange); font-weight: 600; }
  .headline-solar { fill: var(--sun-orange); font-weight: 600; }
  .sun-letter { fill: var(--sun-orange); }
  .brand-dot { fill: var(--sign-white); }
  .brand-name { fill: var(--sign-white); font-weight: 600; letter-spacing: 1px; }
  .phone-number { fill: var(--sign-white); font-weight: 600; }
  .web-address { fill: var(--sign-white); font-weight: 600; letter-spacing: 1px; }
</style>
</head>
<body>
<svg class="yard-sign" viewBox="0 0 1200 900" xmlns="http://www.w3.org/2000/svg">
  <!-- sign body -->
  <path class="sign-outline" d="M82 95 L118 50 L1082 50 L1122 95 L1122 770 L82 770 Z"/>
  <path class="sign-footer" d="M85 488 Q560 610 1119 462 L1125 770 L1125 840 L78 840 L78 770 L85 770 Z"/>

  <!-- headline -->
  <text class="headline" x="182" y="237" font-size="152" textLength="833" lengthAdjust="spacingAndGlyphs">WE'VE GONE</text>

  <text class="headline-solar" x="183" y="456" font-size="258" textLength="112" lengthAdjust="spacingAndGlyphs">S</text>
  <g role="img" aria-label="Sun burst forming the letter O">
    <circle class="sun-letter" cx="432" cy="378" r="68"/>
  </g>
  <text class="headline-solar" x="530" y="456" font-size="258" textLength="472" lengthAdjust="spacingAndGlyphs">LAR!</text>

  <!-- brand -->
  <circle class="brand-dot" cx="148" cy="688" r="34"/>
  <text class="brand-name" x="196" y="684" font-size="38">BRIGHTSIDE</text>
  <text class="brand-name" x="196" y="728" font-size="38">SOLAR</text>

  <!-- contact -->
  <text class="phone-number" x="455" y="700" font-size="108" textLength="630" lengthAdjust="spacingAndGlyphs">555-204-7816</text>
  <text class="web-address" x="460" y="757" font-size="44" textLength="526" lengthAdjust="spacingAndGlyphs">www.brightsidesolar.com</text>
</svg>
</body>
</html>
```